Refresh Application User Interface

Brightmoor wishes to update the look of its business applications. Two representative forms are shown below. Please note, we are not considering changes in functionality or usability. Our goal is a cleaner, more contemporary design.

Industry/Entity Type

Business

```html
<!DOCTYPE html>
<html lang="en">
<head>
<meta charset="utf-8">
<title>Brightmoor — Purchase Order</title>
<link href="https://fonts.googleapis.com/css2?family=Open+Sans:wght@400;600;700;800&display=swap" rel="stylesheet">
<style>
:root{
  --navy:#1b305a;
  --sky:#8db5f5;
  --green:#1f9a40;
  --green-dark:#177a32;
  --toolbar:#1f4f80;
  --tool-sep:#163d66;
  --panel:#f0f0f0;
  --field:#f0f0f0;
  --border:#c9c9c9;
  --text:#222;
  --link:#1a64b4;
  --tab:#c8c8c8;
}
*{box-sizing:border-box;margin:0;padding:0}
html,body{width:1171px;height:1200px;overflow:hidden}
body{background:var(--navy);font-family:"Open Sans",sans-serif;color:var(--text);position:relative}
.app{position:absolute;left:23px;top:23px;width:1125px;height:1125px;background:var(--panel)}
.userbar{position:absolute;left:0;top:0;width:100%;height:39px;background:var(--sky);display:flex;align-items:center;padding:0 15px;font-size:11.5px}
.userbar b{font-size:13px;font-weight:600}
.userbar .rate{margin-left:28px}
.userbar .links{margin-left:auto;font-weight:600;font-size:13px}
.userbar .links span{margin:0 6px}
.mainnav{position:absolute;left:0;top:39px;width:100%;height:51px;background:linear-gradient(#fff,#ececec);display:flex;align-items:center;padding-left:15px;font-size:14.5px;font-weight:600}
.mainnav a{margin-right:36px;color:#111;text-decoration:none;position:relative}
.mainnav a.active{color:var(--green)}
.mainnav a.active::after{content:"";position:absolute;left:50%;bottom:-16px;margin-left:-7px;border:7px solid transparent;border-bottom-color:var(--green)}
.brand{position:absolute;right:18px;top:11px;font-size:22px;font-weight:800;color:#1c3e8a;letter-spacing:.5px}
.subnav{position:absolute;left:0;top:90px;width:100%;height:42px;background:var(--green);display:flex;align-items:center;font-size:13.5px;color:#fff}
.subnav a{padding:0 14px;height:100%;display:flex;align-items:center;color:#fff;text-decoration:none}
.subnav a.active{background:var(--green-dark)}
.subnav .bar{margin:0 4px}
.title{position:absolute;left:15px;top:140px;font-size:19px;font-weight:400}
.viewtabs{position:absolute;right:8px;top:146px;display:flex;font-size:11.5px}
.viewtabs span{height:28px;display:flex;align-items:center;padding:0 13px;background:var(--tab);margin-left:2px;position:relative}
.viewtabs span.on{background:var(--toolbar);color:#fff;font-weight:600;padding:0 17px}
.viewtabs i{position:absolute;right:3px;top:3px;width:8px;height:8px;border-radius:50%;background:#222}
.toolbar{position:absolute;left:8px;top:174px;width:1109px;height:39px;background:var(--toolbar);display:flex;color:#fff;font-size:12.5px}
.toolbar .btn{height:100%;display:flex;align-items:center;justify-content:center;border-right:1px solid var(--tool-sep);gap:6px;padding:0 12px}
.toolbar .icon{width:39px;padding:0}
.toolbar .right{margin-left:auto;display:flex}
.toolbar .right .btn{border-right:none;border-left:1px solid var(--tool-sep);padding:0 16px}
.panel{position:absolute;background:#fff;border:1px solid var(--border)}
.head{left:8px;top:221px;width:1109px;height:320px}
.lbl{position:absolute;font-size:13px;text-align:right;white-space:nowrap}
.fld{position:absolute;height:31px;background:var(--field);border:1px solid var(--border);font-size:11px;display:flex;align-items:center;padding-left:14px}
.fld.white{background:#fff}
.link{position:absolute;font-size:11.5px;color:var(--link)}
.detail{left:8px;top:564px;width:1109px;height:555px}
.sectabs{position:absolute;left:18px;top:22px;display:flex;font-size:11.5px;font-weight:600;color:#555}
.sectabs span{height:29px;display:flex;align-items:center;padding:0 10px;background:var(--tab);margin-right:3px}
.sectabs span.on{background:var(--toolbar);color:#fff}
.secbox{position:absolute;left:18px;top:52px;width:1072px;height:455px;border:1px solid var(--border);border-top:3px solid var(--toolbar)}
.field{position:absolute;width:172px}
.field label{display:block;font-size:12px;margin-bottom:4px}
.select{height:31px;border:1px solid #bbb;background:#fff;font-size:11px;display:flex;align-items:center;padding-left:13px;position:relative}
.select::after{content:"";position:absolute;right:11px;top:13px;border:5px solid transparent;border-top-color:#222;border-bottom:0}
.hint{position:absolute;left:0;width:100%;top:515px;text-align:center;font-size:16px;font-weight:600;color:var(--toolbar)}
.footer{position:absolute;left:0;top:1166px;width:100%;text-align:center;color:#fff;font-size:10.5px}
.mark{position:absolute;right:10px;top:1176px;color:#fff;font-size:10px}
</style>
</head>
<body>
<div class="app">
  <div class="userbar">Logged in As&nbsp;<b>Dana Reyes</b>&nbsp;⚙<span class="rate">Current Rate <b>administrator</b> ▾</span>
    <div class="links">Touch <span>|</span> New Tab <span>|</span> Help <span>|</span> Support <span>|</span> Log out</div>
  </div>
  <nav class="mainnav">
    <a>Home</a><a>eSource</a><a class="active">eBuy</a><a>eRequest</a><a>eSell</a><a>eStock</a><a>ePlan</a><a>Preferences</a>
    <div class="brand">BRIGHTMOOR</div>
  </nav>
  <nav class="subnav">
    <a class="active">Orders</a><a>Receipts</a><a>Shipments</a><a>Invoices</a><a>Pricing</a><span class="bar">|</span><a>Tables</a><a>Reports</a><a>Inquiries</a><a>Periodic Tasks</a><a>Workflows</a>
  </nav>
  <h1 class="title">Purchase Order</h1>
  <div class="viewtabs"><span class="on">Header</span><span>Lines<i></i></span><span>Charges</span><span>Notes<i></i></span></div>
  <div class="toolbar">
    <div class="btn icon"><svg width="16" height="16" viewBox="0 0 16 16"><path d="M11 4 5 10a2 2 0 0 0 3 3l6-6a3.5 3.5 0 0 0-5-5L3 8" fill="none" stroke="#fff" stroke-width="1.6"/></svg></div>
    <div class="btn icon"><svg width="16" height="16" viewBox="0 0 16 16"><path d="M3 1h7l3 3v11H3z" fill="none" stroke="#fff" stroke-width="1.4"/><circle cx="8" cy="9" r="2.5" fill="none" stroke="#fff" stroke-width="1.4"/></svg></div>
    <div class="btn icon"><svg width="16" height="16" viewBox="0 0 16 16"><circle cx="12" cy="3" r="2" fill="#fff"/><circle cx="4" cy="8" r="2" fill="#fff"/><circle cx="12" cy="13" r="2" fill="#fff"/><path d="M12 3 4 8l8 5" stroke="#fff" stroke-width="1.3" fill="none"/></svg></div>
    <div class="btn icon"><svg width="18" height="16" viewBox="0 0 18 16"><rect x="1" y="4" width="16" height="11" rx="1.5" fill="#fff"/><path d="M6 4V2h6v2" stroke="#fff" stroke-width="1.5" fill="none"/><rect x="1" y="8" width="16" height="1.4" fill="#1f4f80"/></svg></div>
    <div class="btn icon"><svg width="16" height="16" viewBox="0 0 16 16"><circle cx="8" cy="8" r="7.5" fill="#fff"/><text x="8" y="12" text-anchor="middle" font-size="11" font-weight="700" fill="#1f4f80" font-family="Open Sans,sans-serif">?</text></svg></div>
    <div class="btn"><svg width="20" height="15" viewBox="0 0 20 15"><rect x="1" y="1" width="18" height="13" fill="none" stroke="#fff" stroke-width="1.4"/><path d="M4 5h12M4 8h12M4 11h12" stroke="#fff" stroke-width="1.2"/></svg>Post Order</div>
    <div class="right">
      <div class="btn"><svg width="15" height="15" viewBox="0 0 15 15"><circle cx="6" cy="6" r="4.6" fill="none" stroke="#fff" stroke-width="1.8"/><path d="M9.5 9.5 14 14" stroke="#fff" stroke-width="2"/></svg>Search</div>
      <div class="btn"><svg width="15" height="15" viewBox="0 0 15 15"><circle cx="7.5" cy="7.5" r="7.5" fill="#fff"/><path d="M7.5 4v7M4 7.5h7" stroke="#1f4f80" stroke-width="2"/></svg>New</div>
      <div class="btn"><svg width="15" height="15" viewBox="0 0 15 15"><circle cx="7.5" cy="7.5" r="7.5" fill="#fff"/><path d="M4 7.5l2.5 2.5L11 5" stroke="#1f4f80" stroke-width="2" fill="none"/></svg>Apply</div>
      <div class="btn"><svg width="15" height="15" viewBox="0 0 15 15"><circle cx="7.5" cy="7.5" r="7.5" fill="#fff"/><path d="M5 5l5 5M10 5l-5 5" stroke="#1f4f80" stroke-width="2"/></svg>Delete</div>
      <div class="btn"><svg width="18" height="14" viewBox="0 0 18 14"><path d="M7 0 0 6l7 6V8c5 0 8 1 11 6-1-6-4-9-11-9z" fill="#fff"/></svg>Back</div>
    </div>
  </div>

  <section class="panel head">
    <div class="lbl" style="left:0;width:90px;top:28px">Order#</div>
    <div class="fld white" style="left:101px;top:20px;width:458px">100159<span style="margin-left:173px;color:var(--green)">Regular Purchase Order</span></div>
    <svg style="position:absolute;left:570px;top:29px" width="17" height="17" viewBox="0 0 17 17"><circle cx="8.5" cy="8.5" r="8" fill="#999"/><path d="M4 5c2 0 3 1 3 3s-2 1-2 3M10 2c0 2 2 2 3 3M11 11c1 1 2 2 1 4" stroke="#fff" stroke-width="1.3" fill="none"/></svg>
    <div class="link" style="right:10px;top:28px">Hold for Completion</div>

    <div class="lbl" style="left:0;width:90px;top:75px">Ship From</div>
    <div class="fld" style="left:101px;top:67px;width:223px">1001</div>
    <div class="lbl" style="left:333px;top:74px">/</div>
    <div class="fld" style="left:350px;top:67px;width:209px">0</div>
    <div class="fld" style="left:101px;top:106px;width:458px">Harborline Clinical Goods</div>
    <div class="lbl" style="left:0;width:90px;top:154px">Address</div>
    <div class="fld" style="left:101px;top:145px;width:458px">14 Linden St</div>
    <div class="fld" style="left:101px;top:184px;width:458px"></div>
    <div class="link" style="left:570px;top:193px">DPV Unconfirmed</div>

    <div class="lbl" style="left:0;width:90px;top:231px">City</div>
    <div class="fld" style="left:101px;top:223px;width:223px">Easton</div>
    <div class="lbl" style="left:330px;width:66px;top:231px">State</div>
    <div class="fld" style="left:406px;top:223px;width:43px">MA</div>
    <div class="fld white" style="left:479px;top:223px;width:31px;padding-left:9px"><svg width="12" height="10" viewBox="0 0 12 10"><path d="M1 5l3.5 3.5L11 1" stroke="#222" stroke-width="2" fill="none"/></svg></div>
    <div class="lbl" style="left:519px;top:231px">Accept</div>

    <div class="lbl" style="left:0;width:90px;top:270px">Zip</div>
    <div class="fld" style="left:101px;top:262px;width:223px">02356-1120</div>
    <div class="lbl" style="left:330px;width:66px;top:270px">Country</div>
    <div class="fld" style="left:406px;top:262px;width:43px">US</div>
    <div class="lbl" style="left:489px;top:270px;text-decoration:underline">Add contact</div>
  </section>

  <section class="panel detail">
    <div class="sectabs"><span>Order Info</span><span class="on">Shipping</span><span>Payment</span><span>Accounts</span><span>Totals / Approval</span></div>
    <div class="secbox">
      <div class="field" style="left:22px;top:26px"><label>Receive At</label><div class="select">ALCH</div></div>
      <div class="field" style="left:22px;top:96px"><label>Carrier</label><div class="select">ParcelLine</div></div>
      <div class="field" style="left:22px;top:166px"><label>Express Service</label><div class="select"></div></div>
      <div class="field" style="left:22px;top:236px"><label>FOB</label><div class="select"></div></div>
      <div class="field" style="left:22px;top:306px"><label>Order Ship Rule</label><div class="select">Partials</div></div>
      <div class="field" style="left:22px;top:376px"><label>Line Ship Rule</label><div class="select">Partials</div></div>

      <div class="field" style="left:448px;top:26px"><label>Request Date</label><div class="select" style="padding-right:0">01/07/2018<svg style="position:absolute;right:11px;top:8px" width="14" height="14" viewBox="0 0 14 14"><rect x="1" y="2" width="12" height="11" fill="none" stroke="#222" stroke-width="1.2"/><path d="M1 5h12M4 0v3M10 0v3M4 7v5M7 7v5M10 7v5M2 9.5h10" stroke="#222" stroke-width="1"/></svg></div></div>
      <div class="field" style="left:448px;top:96px"><label>Freight Terms</label><div class="select">Collect</div></div>
      <div class="field" style="left:448px;top:166px"><label>Freight Calc</label><div class="select"></div></div>

      <div class="field" style="left:873px;top:26px;width:180px"><label>Customer Ship To</label>
        <div style="display:flex;align-items:center"><div class="fld white" style="position:static;width:117px"></div><span style="font-size:11px;margin:0 11px">/</span><div class="fld white" style="position:static;width:31px"></div></div>
      </div>
      <svg style="position:absolute;left:1036px;top:401px" width="13" height="16" viewBox="0 0 13 16"><rect x="0" y="7" width="13" height="9" rx="1" fill="#222"/><path d="M3 7V4.5a3.5 3.5 0 0 1 7 0V7" stroke="#222" stroke-width="2" fill="none"/></svg>
    </div>
    <p class="hint">Enter property values, and click Apply</p>
  </section>
</div>
<div class="footer">Copyright © 2018 Brightmoor.&nbsp; All rights reserved.</div>
<div class="mark">M2</div>
</body>
</html>
```